Modern Attractive Letterhead for Veterinary House Call Business.

A letterhead which can be printed on A4, A5 and A6 paper sizes.
To have: ( our files to be uploaded)
1. Logo with Text
2. telephone
3. email
4. website
5. Address

Target Market(s)

60-85year mainly women pet owners. Also market include families, young professionals, busy people who have dogs and cats

Industry/Entity Type

Business

Requirements
Must have
• 1. Logo with Text ( provided)
• 2. telephone
• 3. email
• 4. website
• 5. Address
Nice to have
• Needs to be modern, preferably warm and caring in nature( if possible )
Should not have
• difficulty in printing A5 and A6

```html
<!DOCTYPE html>
<html lang="en">
<head>
<meta charset="utf-8">
<title>Hearthside Vet Care — Letterhead</title>
<link rel="stylesheet" href="https://fonts.googleapis.com/css2?family=Cinzel:wght@400;600&display=swap">
<style>
  :root {
    --paper: #ffffff;
    --brand-blue: #2b5fae;
    --brand-navy: #2a2a78;
    --brand-green: #5aa23a;
    --sky: #2ea0dc;
    --ink: #2b2b2b;
    --rule: #8a8a8a;
    --watermark: #e8eef6;
  }
  * { margin: 0; padding: 0; box-sizing: border-box; }
  html, body {
    width: 900px;
    height: 1200px;
    overflow: hidden;
    background: var(--paper);
  }
  .letterhead {
    position: relative;
    width: 900px;
    height: 1200px;
    background: var(--paper);
    font-family: "Cinzel", "Times New Roman", serif;
    color: var(--ink);
  }
  .brand {
    position: absolute;
    left: 40px;
    top: 58px;
    display: flex;
    align-items: center;
    gap: 16px;
  }
  .brand-dot {
    width: 44px;
    height: 44px;
    border-radius: 50%;
    background: var(--brand-blue);
  }
  .brand-name {
    font-family: "Cinzel", "Times New Roman", serif;
    font-weight: 600;
    font-size: 36px;
    letter-spacing: 1px;
    color: var(--brand-blue);
    white-space: nowrap;
  }
  .contact {
    position: absolute;
    left: 600px;
    top: 33px;
    padding-left: 14px;
    border-left: 1px solid var(--rule);
    height: 84px;
    font-size: 12.5px;
    line-height: 1.2;
    font-style: normal;
  }
  .contact-line {
    display: flex;
    align-items: center;
    gap: 6px;
    margin-bottom: 6px;
    white-space: nowrap;
  }
  .contact-line svg { width: 12px; height: 12px; flex: none; }
  .contact-address { margin-top: 12px; white-space: nowrap; }
  .watermark {
    position: absolute;
    left: 271px;
    top: 472px;
    width: 400px;
    height: 400px;
    border-radius: 50%;
    background: radial-gradient(circle at 55% 40%, #f1f6fb 0%, var(--watermark) 70%, #eef3f0 100%);
    opacity: 0.8;
  }
  .footer {
    position: absolute;
    left: 0;
    right: 0;
    top: 1164px;
    display: flex;
    justify-content: center;
    align-items: center;
    gap: 14px;
  }
  .footer-rule {
    width: 130px;
    height: 3px;
    background: linear-gradient(90deg, var(--brand-navy), var(--sky));
  }
  .footer-url {
    font-size: 16px;
    letter-spacing: 2.5px;
    color: var(--ink);
    white-space: nowrap;
  }
</style>
</head>
<body>
  <div class="letterhead">
    <header class="brand">
      <span class="brand-dot"></span>
      <span class="brand-name">Hearthside Vet Care</span>
    </header>

    <address class="contact">
      <div class="contact-line">
        <svg viewBox="0 0 12 12" aria-hidden="true">
          <circle cx="6" cy="6" r="5.3" fill="none" stroke="var(--brand-green)" stroke-width="1.2"/>
          <path d="M4 3.2 l1 1.4 -0.6 0.8 q0.8 1.6 2.2 2.2 l0.8 -0.6 1.4 1 -0.8 1 q-3.4 -0.6 -4.8 -4.6z" fill="var(--brand-green)"/>
        </svg>
        <span>0400 315 862</span>
      </div>
      <div class="contact-line">
        <svg viewBox="0 0 12 12" aria-hidden="true">
          <rect x="0.6" y="2.4" width="10.8" height="7.6" rx="1" fill="var(--brand-green)"/>
          <path d="M1.2 3 L6 6.8 L10.8 3" fill="none" stroke="#fff" stroke-width="1"/>
        </svg>
        <span>hello@hearthsidevetcare.com.au</span>
      </div>
      <div class="contact-address">PO Box 2045 Riverbend<br>QLD 4070</div>
    </address>

    <div class="watermark" role="img" aria-label="Faint brand mark watermark"></div>

    <footer class="footer">
      <span class="footer-rule"></span>
      <span class="footer-url">www.hearthsidevetcare.com.au</span>
      <span class="footer-rule"></span>
    </footer>
  </div>
</body>
</html>
```